holloway paving service

Needs to have phone number 0418259730 and email markholloway@brightmail.com.au.
ABN 62318470915
name mark holloway

For all your concreting solutions
Excavation
Exposed & colour concrete
House & shed slabs
Driveways
Landing & steps

Contact Information for Business Card

ph 0418259730
email markholloway@brightmail.com.au.
ABN 62318470915
name mark holloway

```html
<!DOCTYPE html>
<html lang="en">
<head>
<meta charset="utf-8">
<title>Holloway Paving Service – Business Card</title>
<link rel="stylesheet" href="https://fonts.googleapis.com/css2?family=Montserrat:wght@500;600;700&family=Lato:wght@400;700&display=swap">
<style>
  :root {
    --stage: #e8e5e0;
    --slate: #626365;
    --paper: #f3f3f3;
    --orange: #f26522;
    --ink: #5a5b5e;
    --white: #ffffff;
  }
  * { box-sizing: border-box; margin: 0; padding: 0; }
  html, body { width: 1200px; height: 900px; overflow: hidden; background: var(--stage); }
  .stage { position: relative; width: 1200px; height: 900px; }

  .card {
    position: absolute;
    left: 280px;
    width: 640px;
    height: 390px;
    overflow: hidden;
    box-shadow: 0 6px 18px rgba(0,0,0,.18);
  }

  /* Back face */
  .card--back { top: 50px; background: var(--slate); }
  .brand-mark {
    position: absolute; left: 60px; top: 160px;
    display: flex; align-items: center; gap: 14px;
  }
  .brand-mark__square { width: 46px; height: 46px; background: var(--orange); flex: none; }
  .brand-mark__name {
    font-family: "Montserrat", sans-serif; font-weight: 600;
    font-size: 19px; line-height: 1.25; letter-spacing: .5px;
    text-transform: uppercase; color: var(--white);
  }
  .back-divider {
    position: absolute; left: 322px; top: 100px;
    width: 1px; height: 190px; background: rgba(255,255,255,.45);
  }
  .services { position: absolute; left: 346px; top: 104px; color: var(--white); }
  .services__title {
    font-family: "Montserrat", sans-serif; font-weight: 700;
    font-size: 16px; line-height: 1.2; text-transform: uppercase; letter-spacing: .3px;
    margin-bottom: 10px;
  }
  .services__list { list-style: none; font-family: "Lato", sans-serif; font-size: 16px; line-height: 1.45; }
  .services__list li { display: flex; align-items: center; gap: 10px; padding-left: 14px; }
  .services__list li::before {
    content: ""; width: 7px; height: 7px; background: var(--white); transform: rotate(45deg); flex: none;
  }

  /* Front face */
  .card--front { top: 480px; background: var(--paper); }
  .front-wave { position: absolute; inset: 0; }
  .holder-name {
    position: absolute; left: 38px; top: 48px;
    font-family: "Montserrat", sans-serif; font-weight: 700; font-size: 22px;
    text-transform: uppercase; letter-spacing: .3px; color: var(--ink);
  }
  .holder-name__first { color: var(--orange); }
  .front-brand {
    position: absolute; left: 200px; top: 96px;
    display: flex; align-items: center; gap: 16px;
  }
  .front-brand__square { width: 56px; height: 56px; background: var(--orange); flex: none; }
  .front-brand__name {
    font-family: "Montserrat", sans-serif; font-weight: 600; font-size: 22px;
    line-height: 1.2; text-transform: uppercase; letter-spacing: .5px; color: var(--orange);
  }
  .contact { position: absolute; left: 40px; top: 208px; list-style: none;
    font-family: "Lato", sans-serif; font-size: 19px; color: var(--ink); }
  .contact li { display: flex; align-items: center; gap: 10px; line-height: 1.5; }
  .contact svg { width: 16px; height: 16px; flex: none; }
  .abn {
    position: absolute; right: 30px; top: 258px;
    font-family: "Lato", sans-serif; font-size: 15px; letter-spacing: .5px; color: var(--white);
  }
</style>
</head>
<body>
<main class="stage">

  <section class="card card--back" aria-label="Business card back">
    <div class="brand-mark">
      <span class="brand-mark__square"></span>
      <span class="brand-mark__name">Holloway<br>Paving Service</span>
    </div>
    <div class="back-divider"></div>
    <div class="services">
      <h2 class="services__title">For all your<br>concreting solutions</h2>
      <ul class="services__list">
        <li>Excavation</li>
        <li>Exposed &amp; colour concrete</li>
        <li>House &amp; shed slabs</li>
        <li>Driveways</li>
        <li>Landing &amp; steps</li>
      </ul>
    </div>
  </section>

  <section class="card card--front" aria-label="Business card front">
    <svg class="front-wave" viewBox="0 0 640 390" preserveAspectRatio="none" aria-hidden="true">
      <path d="M0 390 L0 364 C200 374 360 300 480 238 C550 204 600 192 640 188 L640 390 Z" fill="var(--slate)"/>
      <path d="M0 326 C180 342 340 304 490 232 C350 312 180 350 0 344 Z" fill="var(--orange)"/>
    </svg>

    <h1 class="holder-name"><span class="holder-name__first">Mark</span> Holloway</h1>

    <div class="front-brand">
      <span class="front-brand__square"></span>
      <span class="front-brand__name">Holloway Paving<br>Service</span>
    </div>

    <ul class="contact">
      <li>
        <svg viewBox="0 0 16 16" aria-hidden="true"><path fill="var(--orange)" d="M3.6 1.5l2.2 2.6-1.3 1.8c.9 2 2.6 3.7 4.6 4.6l1.8-1.3 2.6 2.2-1.2 2.2C6.5 15.4.6 9.5.9 3.3z"/></svg>
        <span>0418259730</span>
      </li>
      <li>
        <svg viewBox="0 0 16 16" aria-hidden="true"><rect x="1" y="3" width="14" height="10" fill="var(--orange)"/><path d="M1.5 3.5L8 9l6.5-5.5" stroke="var(--paper)" stroke-width="1.3" fill="none"/></svg>
        <span>markholloway@brightmail.com.au</span>
      </li>
    </ul>

    <p class="abn">ABN 62318470915</p>
  </section>

</main>
</body>
</html>
```